Business Card Design

WE are looking for a premium quality Business Cards for a Law Firm . Copies of our current business card is attached.

Contact Information for Business Card

xyz

```html
<!DOCTYPE html>
<html lang="en">
<head>
<meta charset="utf-8">
<title>Ashford Lawyers – Business Card</title>
<link rel="stylesheet" href="https://fonts.googleapis.com/css2?family=Open+Sans:wght@400;600;700&display=swap">
<style>
  :root {
    --green: #07301f;
    --green-deep: #04261a;
    --gold: #c9a55a;
    --white: #ffffff;
    --ink: #1d1d1d;
    --backdrop: #dcdcda;
  }
  * { box-sizing: border-box; margin: 0; padding: 0; }
  html, body { width: 1200px; height: 801px; overflow: hidden; }
  body {
    background: var(--backdrop);
    font-family: "Open Sans", Arial, sans-serif;
    position: relative;
  }
  .card {
    position: absolute;
    top: 245px;
    width: 540px;
    height: 310px;
    border-radius: 18px;
    border: 3px solid var(--gold);
    overflow: hidden;
  }
  /* Front */
  .card--front { left: 40px; background: var(--white); color: var(--ink); }
  .front__brand {
    position: absolute; left: 28px; top: 70px; width: 180px;
    display: flex; flex-direction: column; align-items: center; gap: 12px;
  }
  .brand-mark { width: 62px; height: 62px; border-radius: 50%; border: 3px solid var(--gold); }
  .brand-name {
    font-weight: 700; color: var(--green); font-size: 22px; letter-spacing: 1px;
    text-align: center; line-height: 1.15;
  }
  .brand-name span { display: block; font-size: 12px; letter-spacing: 6px; }
  .front__divider {
    position: absolute; left: 226px; top: 40px; width: 2px; height: 180px; background: var(--green);
  }
  .front__details { position: absolute; left: 248px; top: 38px; right: 20px; }
  .person-name { font-size: 26px; font-weight: 700; color: var(--green); line-height: 1.1; }
  .person-title { font-size: 11.5px; color: var(--green); margin-top: 4px; letter-spacing: .2px; }
  .person-creds { font-size: 11.5px; color: var(--green); margin-bottom: 12px; }
  .contact-list { list-style: none; }
  .contact-list li {
    display: flex; align-items: center; gap: 8px; font-size: 12.5px; line-height: 21px;
  }
  .contact-list svg { width: 13px; height: 13px; fill: var(--green); flex: none; }
  .front__address {
    position: absolute; left: 0; right: 0; bottom: 34px; text-align: center;
    font-size: 13.5px; color: var(--ink);
  }
  /* Back */
  .card--back {
    left: 620px;
    background: linear-gradient(160deg, var(--green) 0%, var(--green-deep) 100%);
    color: var(--white);
  }
  .back__brand {
    position: absolute; left: 0; right: 0; top: 22px;
    display: flex; flex-direction: column; align-items: center; gap: 8px;
  }
  .back__brand .brand-mark { width: 50px; height: 50px; }
  .back__brand .brand-name { color: var(--white); font-size: 21px; }
  .tagline {
    position: absolute; left: 0; right: 0; top: 152px; text-align: center;
    color: var(--gold); font-size: 14.5px; letter-spacing: .6px;
  }
  .offices {
    position: absolute; left: 14px; right: 14px; top: 192px;
    display: grid; grid-template-columns: repeat(3, 1fr); gap: 8px; text-align: center;
  }
  .office__city {
    display: inline-block; color: var(--gold); font-weight: 700; font-size: 15px;
    border-bottom: 2px solid var(--gold); padding: 0 6px 1px; margin-bottom: 7px;
  }
  .office__lines { font-size: 10.5px; line-height: 1.45; }
</style>
</head>
<body>

<section class="card card--front" aria-label="Business card front">
  <div class="front__brand">
    <div class="brand-mark"></div>
    <div class="brand-name">ASHFORD<span>LAWYERS</span></div>
  </div>
  <div class="front__divider"></div>
  <div class="front__details">
    <h1 class="person-name">DANIEL MOREAU</h1>
    <p class="person-title">DIRECTOR &amp; PRINCIPAL SOLICITOR</p>
    <p class="person-creds">MBA, Juris Doctor</p>
    <ul class="contact-list">
      <li><svg viewBox="0 0 24 24"><path d="M6.6 10.8a15.1 15.1 0 0 0 6.6 6.6l2.2-2.2c.3-.3.7-.4 1-.2 1.1.4 2.3.6 3.6.6.6 0 1 .4 1 1V20c0 .6-.4 1-1 1A17 17 0 0 1 3 4c0-.6.4-1 1-1h3.5c.6 0 1 .4 1 1 0 1.3.2 2.5.6 3.6.1.3 0 .7-.2 1z"/></svg>+61 73000 4812</li>
      <li><svg viewBox="0 0 24 24"><path d="M7 1h10a2 2 0 0 1 2 2v18a2 2 0 0 1-2 2H7a2 2 0 0 1-2-2V3a2 2 0 0 1 2-2zm0 3v14h10V4z"/></svg>+61 0400 123 456</li>
      <li><svg viewBox="0 0 24 24"><path d="M2 5h20v14H2zm2 2v.5l8 5 8-5V7l-8 5z"/></svg>daniel@ashfordlawyers.com.au</li>
      <li><svg viewBox="0 0 24 24"><path d="M12 2a10 10 0 1 0 0 20 10 10 0 0 0 0-20zm0 2c.9 1.2 1.6 2.6 2 4h-4c.4-1.4 1.1-2.8 2-4zM4.3 14a8 8 0 0 1 0-4h3.4a16 16 0 0 0 0 4zm.8 2h3c.3 1.3.8 2.5 1.4 3.6A8 8 0 0 1 5.1 16zM8 8H5.1a8 8 0 0 1 4.4-3.6C8.8 5.5 8.4 6.7 8 8zm4 12c-.9-1.2-1.6-2.6-2-4h4c-.4 1.4-1.1 2.8-2 4zm2.3-6H9.7a14 14 0 0 1 0-4h4.6a14 14 0 0 1 0 4zm.2 5.6c.6-1.1 1.1-2.3 1.4-3.6h3A8 8 0 0 1 14.5 19.6zM16.3 14a16 16 0 0 0 0-4h3.4a8 8 0 0 1 0 4zM16 8c-.4-1.3-.8-2.5-1.5-3.6A8 8 0 0 1 18.9 8z"/></svg>www.ashfordlawyers.com.au</li>
    </ul>
  </div>
  <p class="front__address">Level 3, Ashford House, 88 Ridge Terrace, Spring Hill, QLD 4000</p>
</section>

<section class="card card--back" aria-label="Business card back">
  <div class="back__brand">
    <div class="brand-mark"></div>
    <div class="brand-name">ASHFORD<span>LAWYERS</span></div>
  </div>
  <p class="tagline">CLEAR ADVICE. STRONG OUTCOMES. ALWAYS</p>
  <div class="offices">
    <div class="office">
      <h2 class="office__city">MELBOURNE</h2>
      <p class="office__lines">Level 12, 240 Harbour Street<br>MELBOURNE, VIC 3000<br>Phone: +61 03 9000 1234</p>
    </div>
    <div class="office">
      <h2 class="office__city">SYDNEY</h2>
      <p class="office__lines">Level 9 Meridian Building<br>18 Market Street<br>PARRAMATTA, NSW 2150<br>Phone: +61 02 9000 5678</p>
    </div>
    <div class="office">
      <h2 class="office__city">PERTH</h2>
      <p class="office__lines">Level 21, Summit Tower<br>75 Swan Terrace<br>Perth, WA 6000<br>Phone: +61 08 9000 2468</p>
    </div>
  </div>
</section>

</body>
</html>
```